Business Cards for IT Consulting Company (Managed Service Provider)

I am looking to have some business cards printed and would like some designs. We are an IT Consulting company based in Vancouver BC. I would like a nice clean and modern look to the cards. I have uploaded all the versions of my logo so parts can be used as needed. Here is a snippit from our website homepage:

Quillbrook Networks Ltd. is an IT Solutions Partner located in Vancouver BC, Canada. We offer IT solutions and support to customers in the greater Vancouver Area. With expertise in Microsoft platforms, as well as Linux and Mac OSX and over 12 years experience in the IT industry, Quillbrook Networks is dedicated to offering our clients top quality service and products. We take pride in the solutions we offer our customers. The greatest compliment a client can give us is to recommend our services.

Quillbrook Networks Ltd. offers a wide range of IT services from onsite service to remote support and managed service solutions. This allows clients to choose the support path that best suits their company’s needs. Supporting many different sized companies from small to enterprise level over the past 12 years Quillbrook Networks has the experience and expertise needed to ensure things run smoothly. Allowing our clients to focus on doing business.

Revolutionizing the way IT services are delivered.

Quillbrook Networks is dedicated to providing our clients with IT solutions that work and grow with them for years to come. This philosophy helps save money in the long run instead of replacing equipment constantly. Far too often IT solutions are not well thought out and while possibly solving the problem at hand, require replacement due to growth or quality within a very short time frame. Quillbrook Networks takes pride in providing solutions that will last and be able to accommodate growth without the need for replacement.

Industry/Entity Type

Information Technology

Contact Information for Business Card

Quillbrook Networks Ltd.
(Employee Name)
Eml: (Employees Email Address)
Web: quillbrook.me
Ph: 604-555-0148

Font styles to use
Serif
Sans Serif

Requirements
Must have
• The Company logo and company colors.
Nice to have
• - Our tag line: "Revolutionizing IT Services" or "Revolutionizing the way IT services are delivered."
• - Also I really like the idea of nature and technology together blending which is sort of where my logo came from so integrating that somehow onto the business cards would be great.

```html
<!DOCTYPE html>
<html lang="en">
<head>
<meta charset="utf-8">
<title>Quillbrook Networks Ltd. – Business Card</title>
<link href="https://fonts.googleapis.com/css2?family=Source+Sans+3:wght@400;600&display=swap" rel="stylesheet">
<style>
  :root {
    --backdrop: #8b8b8b;
    --paper: #f1f1f2;
    --brand-blue: #1592d2;
    --ink-grey: #58595b;
    --band-grey: #555658;
    --rule-grey: #8e8f91;
    --white: #ffffff;
  }
  * { box-sizing: border-box; margin: 0; padding: 0; }
  html, body {
    width: 1105px; height: 1200px; overflow: hidden;
    background: var(--backdrop);
    font-family: "Source Sans 3", "Myriad Pro", sans-serif;
  }
  .card {
    position: absolute; left: 179px; width: 747px; height: 426px;
  }
  .card-front { top: 119px; background: var(--paper); }
  .card-back { top: 636px; background: var(--brand-blue); }

  .wordmark { font-weight: 600; line-height: 1; }
  .front-wordmark {
    position: absolute; right: 42px; top: 46px; text-align: left;
    color: var(--brand-blue);
  }
  .wordmark-name { display: block; font-size: 66px; letter-spacing: -0.5px; }
  .wordmark-suffix { display: block; font-size: 27px; letter-spacing: 0.5px; margin-top: 2px; }

  .holder-name {
    position: absolute; left: 36px; top: 212px;
    font-size: 31px; font-weight: 600; color: var(--brand-blue);
  }
  .name-rule {
    position: absolute; left: 36px; right: 44px; top: 258px;
    height: 2px; background: var(--rule-grey);
  }
  .contact-list {
    position: absolute; left: 38px; top: 270px; list-style: none;
    font-size: 19px; color: var(--ink-grey);
  }
  .contact-list li { display: flex; align-items: center; height: 28.5px; }
  .contact-icon { width: 18px; height: 18px; margin-right: 11px; fill: var(--brand-blue); }
  .office-address {
    position: absolute; right: 42px; top: 298.5px; text-align: right;
    font-style: normal; font-size: 19px; line-height: 28.5px; color: var(--ink-grey);
  }
  .footer-band { position: absolute; left: 0; bottom: 0; width: 747px; height: 45px; }
  .tagline {
    position: absolute; left: 0; width: 488px; bottom: 18px; text-align: center;
    font-size: 19px; font-weight: 600; color: var(--white); line-height: 27px;
  }

  .back-wordmark {
    position: absolute; left: 0; right: 0; top: 158px; text-align: center;
    color: var(--white);
  }
  .back-wordmark .wordmark-name { font-size: 72px; }
  .back-wordmark .wordmark-suffix { font-size: 29px; margin-top: 4px; }
</style>
</head>
<body>
  <section class="card card-front" aria-label="Card front">
    <div class="wordmark front-wordmark">
      <span class="wordmark-name">Quillbrook</span>
      <span class="wordmark-suffix">NETWORKS LTD.</span>
    </div>

    <h1 class="holder-name">Daniel Reyes</h1>
    <div class="name-rule"></div>

    <ul class="contact-list">
      <li>
        <svg class="contact-icon" viewBox="0 0 24 24" aria-hidden="true"><path d="M6.6 10.8a15.1 15.1 0 0 0 6.6 6.6l2.2-2.2a1 1 0 0 1 1-.25 11.4 11.4 0 0 0 3.6.57 1 1 0 0 1 1 1V20a1 1 0 0 1-1 1A17 17 0 0 1 3 4a1 1 0 0 1 1-1h3.5a1 1 0 0 1 1 1c0 1.25.2 2.45.57 3.57a1 1 0 0 1-.25 1z"/></svg>
        604-555-0148
      </li>
      <li>
        <svg class="contact-icon" viewBox="0 0 24 24" aria-hidden="true"><path d="M2 5h20v14H2z M3.5 6.5 12 13l8.5-6.5" fill="var(--brand-blue)"/><path d="M3 6l9 7 9-7" fill="none" stroke="var(--paper)" stroke-width="1.6"/></svg>
        dreyes@quillbrook.me
      </li>
      <li>
        <svg class="contact-icon" viewBox="0 0 24 24" aria-hidden="true"><circle cx="12" cy="12" r="10"/><path d="M2 12h20M12 2c3 3 3 17 0 20M12 2c-3 3-3 17 0 20" fill="none" stroke="var(--paper)" stroke-width="1.4"/></svg>
        www.quillbrook.me
      </li>
    </ul>

    <address class="office-address">
      4126 Cedarvale Road<br>
      Burnaby, British Columbia
    </address>

    <svg class="footer-band" viewBox="0 0 747 45" aria-hidden="true">
      <polygon points="0,0 747,0 747,10 486,10 458,28 0,28" fill="var(--band-grey)"/>
      <polygon points="0,28 458,28 486,10 747,10 747,45 0,45" fill="var(--brand-blue)"/>
    </svg>
    <p class="tagline">Revolutionizing IT Services</p>
  </section>

  <section class="card card-back" aria-label="Card back">
    <div class="wordmark back-wordmark">
      <span class="wordmark-name">Quillbrook</span>
      <span class="wordmark-suffix">NETWORKS LTD.</span>
    </div>
  </section>
</body>
</html>
```